Business Card for Coastal Tundrabridge Advisory

We need a business card for Coastal Tundrabridge Advisory. The company website address is provided below. The company logo is attached. We provide specialized permafrost services to the mining, transportation, and oil & gas industries. The card should be prepared for:
Matthias Korhonen, PhD.
Coastal Tundrabridge Advisory
PO Box 418259
Quillwater, Alaska 99642
Direct: +1-907-555-0143
Email: mkorhonen@tundrabridgeadvisory.example
Website: www.coastaltundrabridgeadvisory.example

```html
<!DOCTYPE html>
<html lang="en">
<head>
<meta charset="utf-8">
<title>Coastal Tundrabridge Advisory — Business Card</title>
<link rel="stylesheet" href="https://fonts.googleapis.com/css2?family=Arimo:wght@400;700&display=swap">
<style>
  :root {
    --backdrop: #e4e4e4;
    --card-light: #f6f6f6;
    --ink: #0f1820;
    --ink-soft: #2a2f35;
    --muted: #555555;
    --band-grey: #525252;
    --paper: #ffffff;
  }
  * { box-sizing: border-box; margin: 0; padding: 0; }
  html, body {
    width: 1200px; height: 1040px; overflow: hidden;
    background: var(--backdrop);
    font-family: "Arimo", Arial, sans-serif;
  }
  .canvas { position: relative; width: 1200px; height: 1040px; }

  .card {
    position: absolute; left: 278px; width: 644px; height: 368px;
    border-radius: 16px; overflow: hidden;
  }
  .card--front { top: 130px; background: var(--card-light); }
  .card--back { top: 568px; background: var(--ink); }

  .front-brand {
    position: absolute; left: 22px; width: 236px; top: 150px;
    text-align: center; color: var(--ink);
    font-weight: 700; font-size: 15px; letter-spacing: 2px; line-height: 1.35;
    text-transform: uppercase;
  }
  .divider {
    position: absolute; left: 271px; top: 96px; width: 1px; height: 170px;
    background: #b5b5b5;
  }
  .details { position: absolute; left: 290px; top: 90px; color: var(--ink-soft); }
  .details__name { font-size: 23px; font-weight: 700; color: var(--ink); line-height: 1; }
  .details__name small { font-size: 18px; }
  .details__title { font-size: 16px; color: var(--muted); margin-top: 5px; margin-left: 2px; }
  .details__address { font-size: 16px; line-height: 20px; margin-top: 12px; }
  .contact { list-style: none; margin-top: 10px; font-size: 15.5px; line-height: 20px; }
  .contact li { display: flex; align-items: center; gap: 8px; }
  .contact svg { width: 13px; height: 13px; flex: none; fill: var(--ink); }

  .band { position: absolute; left: 0; bottom: 0; width: 100%; height: 18px; }

  .back-brand {
    position: absolute; inset: 0;
    display: flex; flex-direction: column; align-items: center; justify-content: center;
    color: var(--paper); text-transform: uppercase; font-weight: 400;
  }
  .back-brand__line { font-size: 36px; letter-spacing: 5px; line-height: 1.3; }
</style>
</head>
<body>
<main class="canvas">
  <section class="card card--front" aria-label="Business card front">
    <div class="front-brand">Coastal Tundrabridge Advisory</div>
    <div class="divider"></div>
    <div class="details">
      <p class="details__name">Matthias Korhonen, <small>PhD.</small></p>
      <p class="details__title">President</p>
      <p class="details__address">PO Box 418259<br>Quillwater, Alaska 99642</p>
      <ul class="contact">
        <li>
          <svg viewBox="0 0 16 16" aria-hidden="true"><path d="M3.6 1.2l2.3 2.6c.4.4.3 1-.1 1.4L4.7 6.3c.9 2 2.9 4 5 5l1.1-1.1c.4-.4 1-.4 1.4-.1l2.6 2.3c.4.4.4 1 0 1.4l-1.5 1.5C10.8 16.4 -.4 5.2.7 2.7L2.2 1.2c.4-.4 1-.4 1.4 0z"/></svg>
          +1-907-555-0143
        </li>
        <li>
          <svg viewBox="0 0 16 16" aria-hidden="true"><path d="M1 3h14v1.2L8 8.8 1 4.2z M1 5.6l7 4.6 7-4.6V13H1z"/></svg>
          mkorhonen@tundrabridgeadvisory.example
        </li>
        <li>
          <svg viewBox="0 0 16 16" aria-hidden="true"><circle cx="8" cy="8" r="7.5"/><path d="M5 4c1.5 0 2 1 3 1.5S7 8 5.5 8 3.5 6 5 4zM9.5 9c1.5 0 2.5 1 2 2.5S10 13.5 9 12s-1-3 .5-3z" fill="#f6f6f6"/></svg>
          www.coastaltundrabridgeadvisory.example
        </li>
      </ul>
    </div>
    <svg class="band" viewBox="0 0 644 18" preserveAspectRatio="none" aria-hidden="true">
      <polygon points="0,0 418,0 414,18 0,18" fill="var(--ink)"/>
      <polygon points="424,0 644,0 644,18 420,18" fill="var(--band-grey)"/>
    </svg>
  </section>

  <section class="card card--back" aria-label="Business card back">
    <div class="back-brand">
      <span class="back-brand__line">Coastal Tundrabridge</span>
      <span class="back-brand__line">Advisory</span>
    </div>
  </section>
</main>
</body>
</html>
```